Web Developer Needs a Business Card Design

I need a personal business card design that represents me as a web developer for potential employers. I would like the background to be a dark color on the front for contrast with my logo and name. The back will have all my information along with a smaller version of the logo. I want something with a modern look and feel, not too conservative. This will be used for potential employers and freelance work.

Industry/Entity Type

Business

Contact Information for Business Card

Front should have my logo and name. The back should have all my personal information which would include: name: Tom Varulek, phone: 570-614-3098, email: tomvarulek@quillbox.net, website url: www.tomvarulek.net, logo, web developer.

Font styles to use
Sans Serif

Requirements
Must have
• Must include my logo. The color palette base color will be the logo color.

```html
<!DOCTYPE html>
<html lang="en">
<head>
<meta charset="utf-8">
<title>Tom Varulek – Business Card</title>
<link rel="stylesheet" href="https://fonts.googleapis.com/css2?family=Questrial&display=swap">
<style>
  :root {
    --backdrop: #8a8b8a;
    --ink-dark: #111312;
    --pattern-tone: #1c2b27;
    --teal: #4fc9aa;
    --paper: #e3e3e3;
    --text-dark: #3d3f3f;
    --white: #f4f4f4;
  }
  * { margin: 0; padding: 0; box-sizing: border-box; }
  html, body {
    width: 1200px; height: 900px; overflow: hidden;
    background: var(--backdrop);
    font-family: "Questrial", "Century Gothic", sans-serif;
  }
  .card {
    position: absolute;
    left: 300px;
    width: 600px; height: 343px;
    overflow: hidden;
  }
  .card--front { top: 90px; background: var(--ink-dark); }
  .card--back  { top: 468px; background: var(--paper); }

  .front-pattern {
    position: absolute; inset: 0;
    background: radial-gradient(ellipse at center, var(--pattern-tone) 0%, #141a18 70%, var(--ink-dark) 100%);
  }
  .front-mark {
    position: absolute; left: 50%; top: 50%;
    transform: translate(-50%, -50%);
    display: flex; align-items: center; gap: 14px;
    padding: 14px 22px;
    background: var(--ink-dark);
    border-radius: 40px;
  }
  .mark-dot {
    width: 30px; height: 30px; border-radius: 50%;
    border: 4px solid var(--teal);
  }
  .mark-name {
    color: var(--teal); font-size: 26px; letter-spacing: 0.5px;
  }

  .back-art { position: absolute; inset: 0; }

  .back-mark {
    position: absolute; right: 34px; top: 74px;
    display: flex; align-items: center; gap: 12px;
  }
  .back-mark .mark-dot { width: 26px; height: 26px; }
  .back-mark .mark-name { font-size: 24px; }

  .identity {
    position: absolute; left: 33px; top: 183px;
    color: var(--text-dark);
  }
  .identity__name { font-size: 28px; line-height: 1; font-weight: 400; }
  .identity__role { font-size: 17px; margin-top: 8px; }

  .contact-list {
    position: absolute; left: 33px; top: 252px;
    list-style: none; color: var(--text-dark);
    font-size: 15px;
  }
  .contact-list li {
    display: flex; align-items: center; gap: 8px;
    height: 23px;
  }
  .contact-list svg { width: 14px; height: 14px; flex: none; }

  .social-list {
    position: absolute; right: 36px; top: 282px;
    list-style: none; display: flex; gap: 10px;
    color: var(--teal); font-size: 13px;
  }
</style>
</head>
<body>

<section class="card card--front">
  <div class="front-pattern" role="img" aria-label="Repeating pattern of the Tom Varulek monogram in dark teal"></div>
  <div class="front-mark">
    <span class="mark-dot"></span>
    <span class="mark-name">Tom Varulek</span>
  </div>
</section>

<section class="card card--back">
  <svg class="back-art" viewBox="0 0 600 343" aria-hidden="true">
    <circle cx="105" cy="312" r="201" fill="var(--teal)"/>
    <circle cx="105" cy="312" r="195" fill="none" stroke="var(--white)" stroke-width="3"/>
  </svg>

  <div class="back-mark">
    <span class="mark-dot"></span>
    <span class="mark-name">Tom Varulek</span>
  </div>

  <div class="identity">
    <h1 class="identity__name">Tom Varulek</h1>
    <p class="identity__role">Front-End Developer</p>
  </div>

  <ul class="contact-list">
    <li>
      <svg viewBox="0 0 14 14"><path d="M3 1 L5.5 1 L6.5 4 L5 5.2 C5.8 7 7 8.2 8.8 9 L10 7.5 L13 8.5 L13 11 C13 12 12 13 11 13 C5.5 12.5 1.5 8.5 1 3 C1 2 2 1 3 1Z" fill="var(--text-dark)"/></svg>
      <span>570-614-3098</span>
    </li>
    <li>
      <svg viewBox="0 0 14 14"><rect x="1" y="3" width="12" height="8" fill="var(--text-dark)"/><path d="M1 3 L7 8 L13 3" fill="none" stroke="var(--teal)" stroke-width="1.2"/></svg>
      <span>tomvarulek@quillbox.net</span>
    </li>
    <li>
      <svg viewBox="0 0 14 14"><circle cx="7" cy="7" r="6" fill="var(--text-dark)"/><path d="M1 7 H13 M7 1 C4 4 4 10 7 13 M7 1 C10 4 10 10 7 13" fill="none" stroke="var(--teal)" stroke-width="1"/></svg>
      <span>www.tomvarulek.net</span>
    </li>
  </ul>

  <ul class="social-list">
    <li>Chirpline</li>
    <li>Workweave</li>
    <li>Codeharbor</li>
  </ul>
</section>

</body>
</html>
```